Business Card & Letterhead Design

We a financial advice company based in Australia. We provide advice to wealthy farmers.

We are changing our business name FROM Brightvale Financial TO Tallowmere Wealth and we need a new letterhead and double sided business card design

Attached is designs from our previous branding (Brightvale Financial) as it includes all the details we require on the new Tallowmere Wealth business cards and letterhead.

Need extra days to review

```html
<!DOCTYPE html>
<html lang="en">
<head>
<meta charset="utf-8">
<title>Tallowmere Wealth Letterhead</title>
<link href="https://fonts.googleapis.com/css2?family=Questrial&display=swap" rel="stylesheet">
<style>
  :root {
    --backdrop: #ececec;
    --paper: #ffffff;
    --ink: #1c1d1f;
    --slate: #5e6469;
    --text: #3a3c3f;
    --rule: #9a9da0;
    --logo-tone: #c4c7ca;
  }
  html, body {
    margin: 0;
    width: 1200px;
    height: 795px;
    overflow: hidden;
    background: var(--backdrop);
    font-family: "Questrial", Arial, sans-serif;
  }
  .letterhead {
    position: absolute;
    left: 333px;
    top: 20px;
    width: 534px;
    height: 755px;
    background: var(--paper);
    box-shadow: 0 2px 10px rgba(0,0,0,0.12);
    overflow: hidden;
  }
  .header-band {
    position: absolute;
    left: 0;
    top: 0;
    width: 340px;
    height: 120px;
    background: linear-gradient(180deg, var(--ink) 0%, var(--ink) 70%, var(--slate) 100%);
  }
  .brand {
    position: absolute;
    left: 28px;
    top: 34px;
    display: flex;
    align-items: center;
    gap: 10px;
    color: var(--logo-tone);
  }
  .brand-circle {
    width: 26px;
    height: 26px;
    border: 1.5px solid var(--logo-tone);
    border-radius: 50%;
  }
  .brand-text { display: flex; flex-direction: column; gap: 4px; }
  .brand-name {
    font-size: 14px;
    letter-spacing: 1.5px;
    text-transform: uppercase;
    white-space: nowrap;
  }
  .brand-tagline {
    font-size: 6px;
    letter-spacing: 2px;
    text-transform: uppercase;
    white-space: nowrap;
  }
  .footer {
    position: absolute;
    right: 26px;
    bottom: 34px;
    display: flex;
    align-items: flex-end;
    gap: 12px;
    color: var(--text);
    font-size: 6.6px;
    line-height: 1.45;
  }
  .footer-block p { margin: 0; white-space: nowrap; }
  .footer-rule {
    width: 1px;
    height: 62px;
    background: var(--rule);
  }
  .footer-label { font-weight: bold; }
  .footer-licensee { margin-bottom: 22px; }
</style>
</head>
<body>
  <main class="letterhead">
    <div class="header-band" role="img" aria-label="Dark curved header sweep with grey and white accent bands"></div>

    <div class="brand">
      <div class="brand-circle"></div>
      <div class="brand-text">
        <span class="brand-name">Tallowmere Wealth</span>
        <span class="brand-tagline">Private Wealth Advisers</span>
      </div>
    </div>

    <footer class="footer">
      <div class="footer-block footer-entity">
        <p>Corrowong Investments Pty Ltd</p>
        <p>ATF The Marrinup Investment</p>
        <p>Trust T/AS Brightvale Financial</p>
        <p>ABN: 48 215 903 116</p>
        <p>Corporate Authorised</p>
        <p>Representative of Westgate</p>
        <p>Advisory Planning Limited</p>
      </div>
      <div class="footer-rule"></div>
      <div class="footer-block footer-contact">
        <p>Suite 4C, 18 Harlow St</p>
        <p>Riverbend QLD 4170</p>
        <p>PO Box 5120</p>
        <p>Riverbend QLD 4170</p>
        <p><span class="footer-label">P:</span> (07) 3000 4812</p>
        <p><span class="footer-label">F:</span> (07) 3000 4813</p>
        <p>www.brightvalefinancial.com.au</p>
        <p>admin@brightvalefinancial.com.au</p>
      </div>
      <div class="footer-rule"></div>
      <div class="footer-block footer-licensee">
        <p>Westgate Advisory Planning Limited</p>
        <p>ABN 62 118 407 335</p>
        <p>Australian Financial Services Licence</p>
        <p>Licence Number 418 902</p>
        <p>Principal Address: 96 Lonsdale St</p>
        <p>PO Box 3310 Melbourne VIC 3000</p>
      </div>
    </footer>
  </main>
</body>
</html>
```